Custom PowerPoint Template for Training & Workshop Presentations

I am looking for a professional designer to create a custom PowerPoint template (PPTX) for my training and workshop materials. My trainings are designed for: HR professionals and Learning & Development specialists;
Executives and team leaders; Organizations investing in employee development and workplace learning; Participants in professional development workshops, seminars, and didactics trainings
The template should therefore appear trustworthy, calm, friendly, structured, and competence‑oriented. The design should be visually appealing, easy to read, and fully editable.

All branding files are attached to this project.
Please use them as the main reference for your design:
Logo (included as attachment)
Brand color specifications (included as attachment)
Font specifications related to the logo and brand (included as attachment)

What I need:
--> Title Slide: Title, subtitle, name, logo
(1–2 variations)
--> Agenda / Overview Slide
--> Content Slides
--> Text only
--> Text + image
-->Two-column
--> Section header
--> Quote / key message
--> Graphic / Model Slides: (1–2 layouts for frameworks, processes, models)
--> Tables & Charts: (Table styles in brand colors; Chart design aligned with typography and color palette)
--> Closing Slide: (Contact or call-to-action; Optional second variation)

All layouts must be built properly inside the PowerPoint Slide Master

```html
<!DOCTYPE html>
<html lang="en">
<head>
<meta charset="utf-8">
<title>Training &amp; Workshop Template – Slide Overview</title>
<link href="https://fonts.googleapis.com/css2?family=Roboto+Condensed:wght@300;400;500;700&display=swap" rel="stylesheet">
<style>
:root{
  --stage:#8e8e8e;
  --navy:#16467f;
  --navy-deep:#1a3a6a;
  --steel:#6b8db8;
  --steel-light:#8aa5c6;
  --footer-light:#6f8fb5;
  --text:#2b3444;
  --white:#ffffff;
}
*{box-sizing:border-box;margin:0;padding:0}
html,body{width:1104px;height:1200px;overflow:hidden;background:var(--stage)}
body{position:relative;font-family:"Roboto Condensed",Arial,sans-serif;color:var(--text)}

.slide-frame{position:absolute;width:453px;height:254px;overflow:hidden;box-shadow:0 2px 6px rgba(0,0,0,.25)}
.slide{position:absolute;left:0;top:0;width:758px;height:425px;transform:scale(.5976);transform-origin:0 0;overflow:hidden;
  background:radial-gradient(ellipse at 75% 70%,#fbf2f0 0%,rgba(251,242,240,0) 45%),linear-gradient(135deg,#f7f8fc 0%,#eef1f7 100%)}
.col-left{left:93px}.col-right{left:559px}
.row-1{top:72px}.row-2{top:339px}.row-3{top:607px}.row-4{top:875px}

/* brand name */
.brand{position:absolute;display:flex;align-items:center;gap:8px}
.brand-dot{width:14px;height:14px;border-radius:50%;background:var(--steel)}
.brand-name{font-weight:500;font-size:17px;color:var(--navy);white-space:nowrap}
.brand.large .brand-dot{width:22px;height:22px}
.brand.large .brand-name{font-size:28px}
.brand-corner{right:28px;top:34px}

.slide-title{position:absolute;left:51px;top:30px;font-size:29px;font-weight:700;letter-spacing:-.2px}
.t-light{color:var(--steel)}.t-dark{color:var(--navy)}

/* footer */
.footer{position:absolute;left:0;bottom:0;width:758px;height:27px;display:flex}
.footer-contact{width:437px;background:var(--footer-light);color:var(--white);font-size:10.5px;font-weight:400;display:flex;align-items:center;padding-left:45px;gap:6px}
.footer-contact svg{width:10px;height:10px;fill:var(--white)}
.footer-social{flex:1;background:var(--navy);display:flex;align-items:center;padding-left:44px;gap:5px}
.social-dot{width:15px;height:15px;border-radius:50%;border:1.6px solid var(--white);display:inline-block}
.page-no{position:absolute;right:19px;bottom:13px;width:22px;height:22px;border-radius:50%;background:var(--steel-light);border:2px solid var(--white);color:var(--white);font-size:8px;font-weight:700;display:flex;align-items:center;justify-content:center}

.photo{position:absolute;border-radius:14px;border:1.5px solid var(--steel)}

/* title slide */
.title-slide .accent-strip{position:absolute;left:0;top:0;width:35px;height:425px;background:#e4e8f0}
.title-slide .accent-bar{position:absolute;left:35px;top:0;width:20px;height:425px;background:var(--footer-light)}
.title-slide .accent-bar-active{position:absolute;left:35px;top:133px;width:20px;height:159px;background:var(--navy)}
.title-main{position:absolute;left:0;right:0;top:0;bottom:0;text-align:center;padding-left:30px}
.title-main .line-1{position:absolute;left:30px;right:0;top:204px;font-size:32px;font-weight:700;color:var(--steel)}
.title-main .line-2{position:absolute;left:30px;right:0;top:246px;font-size:27px;font-weight:700;color:var(--navy)}
.title-main .date{position:absolute;left:0;right:0;top:299px;font-size:16px;font-weight:300;color:#2a5a9a}

/* section divider */
.divider-photo{position:absolute;inset:0;background:radial-gradient(ellipse at 90% 10%,#9fd2e2 0%,rgba(159,210,226,0) 45%),linear-gradient(160deg,#49c2d8 0%,#2a8eb2 35%,#16607f 70%,#0e3f5a 100%)}
.divider-title{position:absolute;right:30px;top:110px;font-size:52px;font-weight:700;color:#1a3f70;letter-spacing:-.3px}

/* agenda */
.agenda-list{position:absolute;left:50px;top:101px;list-style:none}
.agenda-item{display:flex;align-items:center;height:34px;font-size:13px;font-weight:300;color:var(--text)}
.agenda-no{width:28px;height:24px;border:1.5px solid var(--steel-light);border-radius:4px;font-size:10px;font-weight:700;color:var(--navy);display:flex;align-items:center;justify-content:center;margin-right:18px}
.agenda-text{width:241px}
.agenda-page{width:30px}

/* why choose us */
.feature{position:absolute;font-size:12.5px;line-height:20px;font-weight:300;color:var(--text)}
.feature h3{font-size:13px;font-weight:700;color:var(--navy);margin-bottom:3px}
.feature.align-right{text-align:right}

/* body text */
.text-col{position:absolute;top:84px;width:320px;font-size:12.5px;font-weight:300;line-height:24.5px;text-align:justify;color:var(--text)}

/* graph */
.check-item{position:absolute;top:87px;width:205px;display:flex;gap:10px;font-size:8.5px;font-weight:300;line-height:13.5px;color:var(--text)}
.check-dot{flex:none;width:22px;height:22px;border-radius:50%;display:flex;align-items:center;justify-content:center}
.check-dot svg{width:10px;height:10px}
.chart{position:absolute;left:0;top:0}
.chart text{font-family:"Roboto Condensed",Arial,sans-serif}

/* thank you */
.closing-photo{position:absolute;inset:0;background:radial-gradient(circle at 78% 48%,#c9d9f4 0%,#7c9dd6 22%,rgba(124,157,214,0) 42%),linear-gradient(180deg,#7ea2e2 0%,#b9cdef 45%,#dbe6f7 70%,#6d8fcc 100%)}
.closing-title{position:absolute;left:53px;top:118px;font-size:62px;font-weight:700;letter-spacing:-.5px}
.closing-social{position:absolute;left:53px;top:218px;display:flex;gap:6px}
.closing-social .social-dot{border-color:var(--navy-deep);width:16px;height:16px}
</style>
</head>
<body>

<!-- Title slide -->
<section class="slide-frame col-left row-1">
  <div class="slide title-slide">
    <div class="accent-strip"></div>
    <div class="accent-bar"></div>
    <div class="accent-bar-active"></div>
    <div class="brand large" style="left:230px;top:118px">
      <span class="brand-dot"></span><span class="brand-name">Dr. Lena Hartwig-Brandt</span>
    </div>
    <div class="title-main">
      <h1 class="line-1">Successful Goal Achievement With</h1>
      <h2 class="line-2">ZRM and The Individual Motto-Goal</h2>
      <p class="date">March 11,2026</p>
    </div>
  </div>
</section>

<!-- Section divider -->
<section class="slide-frame col-right row-1">
  <div class="slide">
    <div class="divider-photo" role="img" aria-label="Photo of blue puzzle pieces scattered across a teal surface"></div>
    <div class="brand" style="left:375px;top:42px">
      <span class="brand-dot"></span><span class="brand-name">Dr. Lena Hartwig-Brandt</span>
    </div>
    <h2 class="divider-title">Section Divider Title</h2>
  </div>
</section>

<!-- Table of contents -->
<section class="slide-frame col-left row-2">
  <div class="slide">
    <h2 class="slide-title"><span class="t-light">Table Of</span> <span class="t-dark">Contents</span></h2>
    <div class="brand brand-corner"><span class="brand-dot"></span><span class="brand-name">Dr. Lena Hartwig-Brandt</span></div>
    <ol class="agenda-list">
      <li class="agenda-item"><span class="agenda-no">01</span><span class="agenda-text">Sed ut perspiciatis unde omnis</span><span class="agenda-page">03</span></li>
      <li class="agenda-item"><span class="agenda-no">02</span><span class="agenda-text">liste natus error sit voluptatem</span><span class="agenda-page">04</span></li>
      <li class="agenda-item"><span class="agenda-no">03</span><span class="agenda-text">Aaccusantium doloremque laudantium</span><span class="agenda-page">05</span></li>
      <li class="agenda-item"><span class="agenda-no">04</span><span class="agenda-text">Nemo enim ipsam voluptatem quia</span><span class="agenda-page">06</span></li>
      <li class="agenda-item"><span class="agenda-no">05</span><span class="agenda-text">Voluptas sit aspernatur aut odit</span><span class="agenda-page">07</span></li>
      <li class="agenda-item"><span class="agenda-no">06</span><span class="agenda-text">Aut fugitsed quia</span><span class="agenda-page">08</span></li>
    </ol>
    <div class="photo" style="left:457px;top:104px;width:110px;height:108px;background:linear-gradient(135deg,#c9d3dc,#8d9aa6)" role="img" aria-label="Photo of an office window"></div>
    <div class="photo" style="left:600px;top:104px;width:109px;height:108px;background:linear-gradient(135deg,#6b5a4d,#2b2521)" role="img" aria-label="Photo of a smiling workshop participant"></div>
    <div class="photo" style="left:457px;top:245px;width:110px;height:107px;background:linear-gradient(135deg,#b08866,#5a4434)" role="img" aria-label="Photo of a handshake between colleagues"></div>
    <div class="photo" style="left:600px;top:245px;width:109px;height:107px;background:linear-gradient(135deg,#5b4553,#2c2228)" role="img" aria-label="Photo of a team leader in conversation"></div>
    <div class="footer">
      <div class="footer-contact"><svg viewBox="0 0 10 10"><path d="M2 0.5l1.6 2-0.9 1.1a6 6 0 0 0 3.7 3.7l1.1-0.9 2 1.6-0.9 1.6C4.8 9.6 0.4 5.2 0.4 1.4z"/></svg>Call us : +1 555 014 2270 &nbsp;| &nbsp;<svg viewBox="0 0 10 10"><path d="M0 2h10v6H0z M0 2l5 3.5L10 2" fill="none" stroke="#fff" stroke-width="1.2"/></svg>info@hartwigbrandt-training.com</div>
      <div class="footer-social"><span class="social-dot"></span><span class="social-dot"></span><span class="social-dot"></span><span class="social-dot"></span><span class="social-dot"></span></div>
    </div>
    <span class="page-no">02</span>
  </div>
</section>

<!-- Why choose us -->
<section class="slide-frame col-right row-2">
  <div class="slide">
    <h2 class="slide-title"><span class="t-light">Why Choose</span> <span class="t-dark">Us</span></h2>
    <div class="brand brand-corner"><span class="brand-dot"></span><span class="brand-name">Dr. Lena Hartwig-Brandt</span></div>
    <svg class="chart" width="758" height="425" viewBox="0 0 758 425" aria-hidden="true">
      <g fill="none" stroke="#8aa5c6" stroke-width="1">
        <polyline points="216,137 216,172 280,172"/>
        <polyline points="485,110 410,110"/>
        <polyline points="544,273 544,238 470,238"/>
        <polyline points="279,297 340,297"/>
      </g>
      <g fill="#16467f"><circle cx="216" cy="137" r="2.5"/><circle cx="485" cy="110" r="2.5"/><circle cx="544" cy="273" r="2.5"/><circle cx="279" cy="297" r="2.5"/></g>
      <g transform="translate(381,207) rotate(45)">
        <rect x="-88" y="-88" width="86" height="86" fill="#16467f"/>
        <rect x="2" y="-88" width="86" height="86" fill="#6b8db8"/>
        <rect x="-88" y="2" width="86" height="86" fill="#6b8db8"/>
        <rect x="2" y="2" width="86" height="86" fill="#16467f"/>
      </g>
      <g fill="#fff">
        <circle cx="381" cy="140" r="6"/><path d="M370 156a11 8 0 0 1 22 0z"/>
        <rect x="306" y="195" width="22" height="15" rx="1.5"/><rect x="313" y="212" width="8" height="3"/>
        <path d="M434 195h10l6 6v16h-16z"/>
        <path d="M372 275l16-16 5 5-16 16h-5z"/>
      </g>
    </svg>
    <div class="feature align-right" style="right:556px;top:116px;width:190px"><h3>NUMQUAM EIUS</h3>Nemo enim ipsam voluptatem quia voluptas sit aspernatur aut odit aut fugquia consequuntur magni</div>
    <div class="feature" style="left:502px;top:98px;width:220px"><h3>NUMQUAM EIUS</h3>Nemo enim ipsam voluptatem quia voluptas sit aspernatur aut odit aut fugit, sed quia consequuntur magni dolores</div>
    <div class="feature" style="left:559px;top:266px;width:180px"><h3>NUMQUAM EIUS</h3>Nemo enim ipsam voluptatem quia voluptas sit aspernatur aut odit aut fugit, sed quia consequuntur</div>
    <div class="feature align-right" style="right:494px;top:288px;width:240px"><h3>NUMQUAM EIUS</h3>Nemo enim ipsam voluptatem quia voluptas sit aspernatur aut odit aut fugit, sed quia consequuntur magni dolores eos</div>
    <div class="footer">
      <div class="footer-contact"><svg viewBox="0 0 10 10"><path d="M2 0.5l1.6 2-0.9 1.1a6 6 0 0 0 3.7 3.7l1.1-0.9 2 1.6-0.9 1.6C4.8 9.6 0.4 5.2 0.4 1.4z"/></svg>Call us : +1 555 014 2270 &nbsp;| &nbsp;<svg viewBox="0 0 10 10"><path d="M0 2h10v6H0z M0 2l5 3.5L10 2" fill="none" stroke="#fff" stroke-width="1.2"/></svg>info@hartwigbrandt-training.com</div>
      <div class="footer-social"><span class="social-dot"></span><span class="social-dot"></span><span class="social-dot"></span><span class="social-dot"></span><span class="social-dot"></span></div>
    </div>
    <span class="page-no">06</span>
  </div>
</section>

<!-- About us -->
<section class="slide-frame col-left row-3">
  <div class="slide">
    <h2 class="slide-title"><span class="t-light">About</span> <span class="t-dark">Us</span></h2>
    <div class="brand brand-corner"><span class="brand-dot"></span><span class="brand-name">Dr. Lena Hartwig-Brandt</span></div>
    <p class="text-col" style="left:51px">Resilience describes the ability to cope with stress and crises, leading to personal growth. This workshop will therefore begin by focusing participants' attention on the benefits of a resilient lifestyle using the seven resilience factors. The second step will sharpen awareness of stress and its various forms. Participants will learn to identify energy boosters and drainers and develop individual coping strategies. They will be introduced to models and methods that can help them optimize their studies and their upcoming career entry. Prioritization and setting action and outcome goals are relevant aspects of this process.</p>
    <p class="text-col" style="left:408px">To improve personal mental resilience, it is important to recognize and reflect on one's own thought patterns. Therefore, the workshop will focus on reflecting on one's personal definition of meaning. The resource check consciously highlights one's own competencies. Since social contacts in the sense of networking/cooperation are another building block for developing resilience and shaping one's individual career path, opportunities will be presented to utilize, establish, and expand a corresponding social network.</p>
    <div class="footer">
      <div class="footer-contact"><svg viewBox="0 0 10 10"><path d="M2 0.5l1.6 2-0.9 1.1a6 6 0 0 0 3.7 3.7l1.1-0.9 2 1.6-0.9 1.6C4.8 9.6 0.4 5.2 0.4 1.4z"/></svg>Call us : +1 555 014 2270 &nbsp;| &nbsp;<svg viewBox="0 0 10 10"><path d="M0 2h10v6H0z M0 2l5 3.5L10 2" fill="none" stroke="#fff" stroke-width="1.2"/></svg>info@hartwigbrandt-training.com</div>
      <div class="footer-social"><span class="social-dot"></span><span class="social-dot"></span><span class="social-dot"></span><span class="social-dot"></span><span class="social-dot"></span></div>
    </div>
    <span class="page-no">03</span>
  </div>
</section>

<!-- Graph -->
<section class="slide-frame col-right row-3">
  <div class="slide">
    <h2 class="slide-title"><span class="t-light">Our</span> <span class="t-dark">Graph</span></h2>
    <div class="brand brand-corner"><span class="brand-dot"></span><span class="brand-name">Dr. Lena Hartwig-Brandt</span></div>
    <div class="check-item" style="left:55px"><span class="check-dot" style="background:var(--steel)"><svg viewBox="0 0 10 10"><path d="M1.5 5l2.5 2.5 4.5-5" fill="none" stroke="#fff" stroke-width="1.4"/></svg></span><span>Sed ut perspiciatis unde omnis iste natussit voluptatem accus doloremque laudantium, totam rem vitae dicta sunt explicabo.</span></div>
    <div class="check-item" style="left:281px"><span class="check-dot" style="background:var(--navy)"><svg viewBox="0 0 10 10"><path d="M1.5 5l2.5 2.5 4.5-5" fill="none" stroke="#fff" stroke-width="1.4"/></svg></span><span>Sed ut perspiciatis unde omnis iste natussit voluptatem accus doloremque laudantium, totam rem vitae dicta sunt explicabo.</span></div>
    <div class="check-item" style="left:507px"><span class="check-dot" style="background:var(--steel-light)"><svg viewBox="0 0 10 10"><path d="M1.5 5l2.5 2.5 4.5-5" fill="none" stroke="#fff" stroke-width="1.4"/></svg></span><span>Sed ut perspiciatis unde omnis iste natussit voluptatem accus doloremque laudantium, totam rem vitae dicta sunt explicabo.</span></div>
    <svg class="chart" width="758" height="425" viewBox="0 0 758 425" role="img" aria-label="Bar chart of values for 2016, 2017 and 2018 by region">
      <g font-size="7" fill="#2b3444">
        <rect x="350" y="158" width="5" height="5" fill="#6b8db8"/><text x="357" y="163">2016</text>
        <rect x="381" y="158" width="5" height="5" fill="#1a4a85"/><text x="388" y="163">2017</text>
        <rect x="412" y="158" width="5" height="5" fill="#1a3a6a"/><text x="419" y="163">2018</text>
      </g>
      <g font-size="7" fill="#2b3444" text-anchor="end">
        <text x="136" y="177">100</text><text x="136" y="212">80</text><text x="136" y="248">60</text><text x="136" y="283">40</text><text x="136" y="319">20</text><text x="136" y="354">0</text>
      </g>
      <g>
        <rect x="168" y="227.4" width="23" height="124.6" fill="#6b8db8"/><rect x="197" y="236.3" width="23" height="115.7" fill="#1a4a85"/><rect x="225" y="280.8" width="23" height="71.2" fill="#1a3a6a"/>
        <rect x="297" y="200.7" width="23" height="151.3" fill="#6b8db8"/><rect x="326" y="257.7" width="23" height="94.3" fill="#1a4a85"/><rect x="354" y="307.5" width="23" height="44.5" fill="#1a3a6a"/>
        <rect x="427" y="232.7" width="23" height="119.3" fill="#6b8db8"/><rect x="456" y="273.7" width="23" height="78.3" fill="#1a4a85"/><rect x="484" y="320" width="23" height="32" fill="#1a3a6a"/>
        <rect x="556" y="200.7" width="23" height="151.3" fill="#6b8db8"/><rect x="585" y="293.3" width="23" height="58.7" fill="#1a4a85"/><rect x="613" y="264.8" width="23" height="87.2" fill="#1a3a6a"/>
      </g>
      <g font-size="10" fill="#2b3444" text-anchor="middle">
        <text x="179.5" y="223">70</text><text x="208.5" y="232">65</text><text x="236.5" y="276">40</text>
        <text x="308.5" y="196">85</text><text x="337.5" y="253">53</text><text x="365.5" y="303">25</text>
        <text x="438.5" y="228">67</text><text x="467.5" y="269">44</text><text x="495.5" y="316">18</text>
        <text x="567.5" y="196">85</text><text x="596.5" y="289">33</text><text x="624.5" y="260">49</text>
      </g>
      <g font-size="7" fill="#2b3444" text-anchor="middle">
        <text x="208" y="365">Eruope</text><text x="337" y="365">Asia</text><text x="467" y="365">North America</text><text x="596" y="365">South America</text>
      </g>
    </svg>
    <div class="footer">
      <div class="footer-contact"><svg viewBox="0 0 10 10"><path d="M2 0.5l1.6 2-0.9 1.1a6 6 0 0 0 3.7 3.7l1.1-0.9 2 1.6-0.9 1.6C4.8 9.6 0.4 5.2 0.4 1.4z"/></svg>Call us : +1 555 014 2270 &nbsp;| &nbsp;<svg viewBox="0 0 10 10"><path d="M0 2h10v6H0z M0 2l5 3.5L10 2" fill="none" stroke="#fff" stroke-width="1.2"/></svg>info@hartwigbrandt-training.com</div>
      <div class="footer-social"><span class="social-dot"></span><span class="social-dot"></span><span class="social-dot"></span><span class="social-dot"></span><span class="social-dot"></span></div>
    </div>
    <span class="page-no">07</span>
  </div>
</section>

<!-- Learning objectives -->
<section class="slide-frame col-left row-4">
  <div class="slide">
    <h2 class="slide-title"><span class="t-light">Learning</span> <span class="t-dark">Objectives</span></h2>
    <div class="brand brand-corner"><span class="brand-dot"></span><span class="brand-name">Dr. Lena Hartwig-Brandt</span></div>
    <p class="text-col" style="left:51px">During the course of scientific projects, one is often confronted not only with content-related and methodological challenges, but also with motivational highs and lows. Short-term daily, weekly, or monthly plans help to keep track of milestones. Nevertheless, personal motivation and thus one's inner attitude toward the project are crucial for achieving goals successfully. In this workshop, participants will have the opportunity to develop an individual motto goal using the scientific method known as the Zurich Resource Model (ZRM). Motto goals increase individual identification with the goal and boost intrinsic motivation in the long term. Considering the long timeframe of scientific projects,</p>
    <div class="photo" style="left:457px;top:103px;width:110px;height:108px;background:linear-gradient(135deg,#9a8a7c,#4a403a)" role="img" aria-label="Photo of a workshop participant in an office"></div>
    <div class="photo" style="left:600px;top:103px;width:109px;height:108px;background:linear-gradient(135deg,#7d8a95,#2e3a46)" role="img" aria-label="Photo of colleagues shaking hands"></div>
    <div class="photo" style="left:457px;top:244px;width:110px;height:108px;background:linear-gradient(135deg,#b5b5b5,#6a6a6a)" role="img" aria-label="Photo of a team seen from above"></div>
    <div class="photo" style="left:600px;top:244px;width:109px;height:108px;background:linear-gradient(135deg,#a7a29c,#5e5650)" role="img" aria-label="Photo of a group meeting seen from above"></div>
    <div class="footer">
      <div class="footer-contact"><svg viewBox="0 0 10 10"><path d="M2 0.5l1.6 2-0.9 1.1a6 6 0 0 0 3.7 3.7l1.1-0.9 2 1.6-0.9 1.6C4.8 9.6 0.4 5.2 0.4 1.4z"/></svg>Call us : +1 555 014 2270 &nbsp;| &nbsp;<svg viewBox="0 0 10 10"><path d="M0 2h10v6H0z M0 2l5 3.5L10 2" fill="none" stroke="#fff" stroke-width="1.2"/></svg>info@hartwigbrandt-training.com</div>
      <div class="footer-social"><span class="social-dot"></span><span class="social-dot"></span><span class="social-dot"></span><span class="social-dot"></span><span class="social-dot"></span></div>
    </div>
    <span class="page-no">04</span>
  </div>
</section>

<!-- Thank you -->
<section class="slide-frame col-right row-4">
  <div class="slide">
    <div class="closing-photo" role="img" aria-label="Photo of a globe assembled from blue puzzle pieces"></div>
    <div class="brand large" style="left:67px;top:56px">
      <span class="brand-dot"></span><span class="brand-name" style="font-size:22px">Dr. Lena Hartwig-Brandt</span>
    </div>
    <h2 class="closing-title"><span style="color:#1a3f70">Thank</span> <span class="t-light">You</span></h2>
    <div class="closing-social"><span class="social-dot"></span><span class="social-dot"></span><span class="social-dot"></span><span class="social-dot"></span><span class="social-dot"></span></div>
  </div>
</section>

</body>
</html>
```